THE WELLNESS BARN WEBSITE for Physio, Fitness, health

An attractive website advertising a physiotherapyand fitness / gym business, not generic, colours are natural, greens, browns, beiges. No cheesy pictures. With the ability to sell a small,amount of goods online if i decide to. Simple to navigate. Text boxes that i can input the main information and change easily. Somewhere to put my timetable. Easy to find contact details. However many pages it needs, im not fussed.
Target Market(s)
People looking for rehabilitation or fitness classes
Industry/Entity Type
Physiotherapy, Fitness, Gym, Health
Coding
Coded - Design and coding required
Number of Pages Required
1 page
Font styles to use
Other font styles liked:
- Im not fusse,ld, not script
Requirements
Must have
- Will upload posts from my business insta page for reference about the feel. Earthy natural tones, I have a lot of timber, and rustic looking piece's, plants etc in my clinic
Nice to have
- Simple to navigate
Should not have
- Cheesy "yoga" or generic "people doing physio" pics

```html
<!DOCTYPE html>
<html lang="en">
<head>
<meta charset="utf-8">
<title>The Wellness Barn Kestrel Bay</title>
<link rel="stylesheet" href="https://fonts.googleapis.com/css2?family=Oswald:wght@500;600&family=Montserrat:wght@400;500;600;700&display=swap">
<style>
:root{
  --cream:#efe8d8;
  --card:#e7dbbf;
  --green:#2e4a2b;
  --green-dark:#24391f;
  --brown:#8a5a3b;
  --brown-deep:#784a2e;
  --ink:#1f1f1f;
  --muted:#4a4a4a;
  --star:#e39b1c;
  --white:#ffffff;
}
*{box-sizing:border-box;margin:0;padding:0}
html,body{width:1200px;height:4648px;overflow:hidden}
body{position:relative;background:var(--cream);font-family:"Montserrat",sans-serif;color:var(--ink)}
.abs{position:absolute}
.head{font-family:"Oswald",sans-serif;font-weight:500;text-align:center;left:0;width:1200px}
.underline{left:505px;width:190px;height:5px;border-radius:50%;background:var(--brown)}
.centertxt{text-align:center;left:0;width:1200px}
.btn{position:absolute;border-radius:22px;font-weight:700;font-size:14px;color:var(--white);display:flex;align-items:center;justify-content:center;letter-spacing:.3px}
.arrow{position:absolute;width:40px;height:40px;border-radius:50%;border:2px solid #333;display:flex;align-items:center;justify-content:center}
.arrow.light{border-color:#888}
.brandname{font-weight:700;color:var(--green);font-size:21px;line-height:1.1;display:flex;align-items:center;gap:10px}
.brandname .dot{width:22px;height:22px;border-radius:50%;background:var(--green);flex:none}

/* header */
.site-header{top:0;left:0;width:1200px;height:128px;background:var(--cream)}
.contact{top:12px;font-size:13px;display:flex;align-items:center;gap:10px;color:var(--brown)}
.contact b{font-weight:500}
.contact span{color:var(--ink)}
.contact .ico{width:36px;height:36px;border-radius:50%;background:var(--green);display:flex;align-items:center;justify-content:center}
.nav{top:76px;left:333px;display:flex;gap:44px;font-size:13px;font-weight:500}
.nav .active{font-weight:700;border-bottom:2px solid var(--green);padding-bottom:10px}

/* hero */
.hero{top:128px;left:0;width:1200px;height:558px;background:radial-gradient(ellipse at 50% 60%,#3a1a18 0%,#22100f 55%,#120808 100%)}
.hero-glow{top:0;left:0;width:1200px;height:558px;background:linear-gradient(90deg,rgba(200,20,20,.35),transparent 25%,transparent 75%,rgba(200,20,20,.35))}

/* offer cards */
.offer-card{top:1058px;width:287px;height:338px;color:var(--white)}
.offer-card h3{position:absolute;left:22px;font-size:19px;font-weight:500;line-height:1.55}
.offer-card p{position:absolute;left:24px;top:238px;width:250px;font-size:13px;line-height:27px}
.offer-card .bar{position:absolute;left:22px;height:4px;width:80px;background:var(--green)}

/* products */
.product{top:1681px;width:296px;height:320px;border-radius:8px}
.product .icons{position:absolute;right:14px;top:18px;display:flex;flex-direction:column;gap:16px}
.product .icons div{width:40px;height:40px;border-radius:50%;background:var(--white);display:flex;align-items:center;justify-content:center}
.prodinfo{top:1948px;width:255px;height:106px;background:var(--white);border-radius:4px;text-align:center}
.prodinfo h4{font-size:19px;font-weight:700;margin-top:15px}
.stars{color:var(--star);font-size:14px;letter-spacing:1px}
.price{font-size:22px;margin-top:4px}
.price small{font-size:13px;text-decoration:line-through;margin-right:8px}

/* reviews */
.review{top:2285px;width:310px;height:302px;background:var(--card);box-shadow:0 2px 8px rgba(0,0,0,.2)}
.review p{position:absolute;left:24px;top:36px;width:270px;font-size:14px;line-height:28px}
.review .rule{position:absolute;left:28px;top:165px;width:255px;height:1px;background:#7a6a4a}
.review .avatar{position:absolute;left:12px;top:185px;width:94px;height:94px;border-radius:50%;background:linear-gradient(#9b7a5f,#5a4232)}
.review .who{position:absolute;left:122px;top:192px}
.review .who b{display:block;color:var(--brown);font-size:16px;font-weight:700}
.review .who span{display:block;font-size:14px;margin:6px 0 4px}
.review .badge{position:absolute;right:16px;top:222px;width:32px;height:32px;border-radius:50%;background:#5a7fc0}

/* team */
.team{top:2750px;left:0;width:1200px;height:725px;background:var(--brown-deep)}
.teamcard{top:3093px;left:262px;width:668px;height:279px;background:var(--card);border-radius:36px;border:5px solid #d6c39a}

/* faq */
.faq-item{left:612px;width:433px;height:87px;border-bottom:2px solid var(--green);font-size:16px;font-weight:500;display:flex;justify-content:space-between;align-items:center;padding:0 4px}

/* footer */
.site-footer{top:4232px;left:0;width:1200px;height:416px;background:var(--green)}
.fnav{top:4512px;left:253px;display:flex;gap:43px;font-size:14px;color:var(--white)}
</style>
</head>
<body>

<!-- Header -->
<header class="abs site-header">
  <div class="abs brandname" style="left:112px;top:40px;width:160px">
    <span class="dot"></span><span>The Wellness<br>Barn</span>
  </div>
  <div class="abs contact" style="left:496px">
    <div class="ico"><svg width="18" height="14" viewBox="0 0 18 14"><rect x="1" y="1" width="16" height="12" rx="1" fill="none" stroke="#fff" stroke-width="1.6"/><path d="M1 2l8 6 8-6" fill="none" stroke="#fff" stroke-width="1.6"/></svg></div>
    <b>Email Us</b> <span>info@wellnessbarnkestrel.com</span>
  </div>
  <div class="abs contact" style="left:872px">
    <div class="ico"><svg width="18" height="18" viewBox="0 0 24 24"><path d="M6 3l3 4-2 2c1 3 4 6 7 7l2-2 4 3-2 4C10 21 3 14 3 5z" fill="#fff"/></svg></div>
    <b>Call Us</b> <span>+61 7 4000 1234</span>
  </div>
  <nav class="abs nav">
    <span class="active">HOME</span><span>ABOUT US</span><span>SERVICES</span><span>OUR PRODUCTS</span><span>TESTIMONIALS</span><span>CONTACT</span>
  </nav>
  <svg class="abs" style="left:1064px;top:70px" width="24" height="26" viewBox="0 0 24 26"><path d="M3 8h18l-1 16H4z" fill="none" stroke="#222" stroke-width="2"/><path d="M8 8V5a4 4 0 018 0v3" fill="none" stroke="#222" stroke-width="2"/></svg>
</header>

<!-- Hero -->
<section class="abs hero" role="img" aria-label="Dark gym hall lit by red neon strips">
  <div class="abs hero-glow"></div>
  <div class="abs head" style="top:110px;font-size:30px;color:#fff">WELCOME TO</div>
  <div class="abs head" style="top:148px;font-size:54px;color:#fff">THE WELLNESS BARN KESTREL BAY</div>
  <p class="abs centertxt" style="top:232px;left:260px;width:680px;color:#fff;font-size:14px;line-height:30px">Discover a healthier you with our Physiotherapist led programs. At The Wellness Barn Kestrel Bay, we focus on safe and effective movement to enhance your quality of life. Join us for a comprehensive approach to wellbeing.</p>
  <div class="btn" style="left:508px;top:342px;width:176px;height:44px;background:var(--brown)">GET STARTED</div>
</section>

<!-- Offer -->
<h2 class="abs head" style="top:772px;font-size:38px">What do we have to offer?</h2>
<div class="abs underline" style="top:848px"></div>
<p class="abs centertxt" style="top:876px;left:200px;width:800px;font-size:13px;line-height:27.5px">The Wellness Barn Kestrel Bay is dedicated to empowering individuals to achieve their health and wellbeing goals through safe and effective movement. Our core values include Integrity, Collaboration, Inclusivity, and a strong Commitment to health. We believe in providing professional support tailored to each individual's needs. Our team, including experienced professionals like Dr. Clara Whitfield and Mark Delaney, is committed to guiding you on your wellness journey. Join us in fostering a healthier community where everyone can thrive.</p>

<div class="abs offer-card" style="left:110px;background:linear-gradient(#9aa69a,#4a5a4e)" role="img" aria-label="Group stretching in a bright studio">
  <h3 style="top:152px">Physiotherapy Classes<br>for Everyone</h3>
  <div class="bar" style="top:222px"></div>
  <p>Our classes are tailored for all ages, focusing on safe movement to enhance mobility</p>
</div>
<div class="abs offer-card" style="left:428px;background:linear-gradient(#7a4e2a,#2a1a10)" role="img" aria-label="Person relaxing in a warm lit room">
  <h3 style="top:236px">Holistic Wellness<br>Programs</h3>
  <div class="bar" style="top:305px"></div>
</div>
<div class="abs offer-card" style="left:745px;background:linear-gradient(#8f9a8a,#5a4a3e)" role="img" aria-label="Smiling friends after a workout">
  <h3 style="top:230px">Mindfulness and Yoga<br>Sessions</h3>
  <div class="bar" style="top:300px"></div>
</div>
<div class="abs offer-card" style="left:1061px;width:139px;background:linear-gradient(#9a8a6a,#4a3a2a)" role="img" aria-label="Personalized nutrition session">
  <h3 style="top:262px">Personalized</h3>
</div>
<div class="arrow light" style="left:32px;top:1208px"><svg width="14" height="14" viewBox="0 0 14 14"><path d="M9 2L4 7l5 5" fill="none" stroke="#888" stroke-width="2"/></svg></div>
<div class="arrow" style="left:1115px;top:1208px"><svg width="14" height="14" viewBox="0 0 14 14"><path d="M5 2l5 5-5 5" fill="none" stroke="#222" stroke-width="2"/></svg></div>

<!-- Products -->
<section class="abs" style="top:1508px;left:0;width:1200px;height:334px;background:var(--green)"></section>
<h2 class="abs head" style="top:1564px;font-size:38px;color:#fff">Our Products</h2>
<div class="abs underline" style="top:1640px;background:#fff"></div>

<div class="abs product" style="left:114px;background:linear-gradient(135deg,#c47a4a,#8a8a80)" role="img" aria-label="Cap and t-shirt merchandise">
  <div class="icons"><div><svg width="20" height="18" viewBox="0 0 20 18"><path d="M10 17S1 11 1 5a4.5 4.5 0 019-1 4.5 4.5 0 019 1c0 6-9 12-9 12z" fill="none" stroke="#222" stroke-width="1.8"/></svg></div><div><svg width="20" height="18" viewBox="0 0 20 18"><path d="M1 1h3l2 11h11l2-8H5" fill="none" stroke="#222" stroke-width="1.8"/><circle cx="8" cy="16" r="1.5" fill="#222"/><circle cx="16" cy="16" r="1.5" fill="#222"/></svg></div></div>
</div>
<div class="abs product" style="left:455px;background:linear-gradient(135deg,#b99a7a,#c26a3a)" role="img" aria-label="Wheat bag heat pack in gift box">
  <div class="icons"><div><svg width="20" height="18" viewBox="0 0 20 18"><path d="M10 17S1 11 1 5a4.5 4.5 0 019-1 4.5 4.5 0 019 1c0 6-9 12-9 12z" fill="none" stroke="#222" stroke-width="1.8"/></svg></div><div><svg width="20" height="18" viewBox="0 0 20 18"><path d="M1 1h3l2 11h11l2-8H5" fill="none" stroke="#222" stroke-width="1.8"/><circle cx="8" cy="16" r="1.5" fill="#222"/><circle cx="16" cy="16" r="1.5" fill="#222"/></svg></div></div>
</div>
<div class="abs product" style="left:795px;background:linear-gradient(135deg,#6a6a3a,#5a3a3a)" role="img" aria-label="Sweat bands among leaves">
  <div class="icons"><div><svg width="20" height="18" viewBox="0 0 20 18"><path d="M10 17S1 11 1 5a4.5 4.5 0 019-1 4.5 4.5 0 019 1c0 6-9 12-9 12z" fill="none" stroke="#222" stroke-width="1.8"/></svg></div><div><svg width="20" height="18" viewBox="0 0 20 18"><path d="M1 1h3l2 11h11l2-8H5" fill="none" stroke="#222" stroke-width="1.8"/><circle cx="8" cy="16" r="1.5" fill="#222"/><circle cx="16" cy="16" r="1.5" fill="#222"/></svg></div></div>
</div>
<div class="abs prodinfo" style="left:135px"><h4>Cap And T Shirts</h4><div class="stars">★★★★★</div><div class="price"><small>$93.88</small>$54.49</div></div>
<div class="abs prodinfo" style="left:476px"><h4>Wheat Bag</h4><div class="stars">★★★★★</div><div class="price"><small>$93.88</small>$54.49</div></div>
<div class="abs prodinfo" style="left:816px"><h4>Sweat Band</h4><div class="stars">★★★★★</div><div class="price"><small>$93.88</small>$54.49</div></div>
<div class="arrow light" style="left:38px;top:1861px"><svg width="14" height="14" viewBox="0 0 14 14"><path d="M9 2L4 7l5 5" fill="none" stroke="#888" stroke-width="2"/></svg></div>
<div class="arrow" style="left:1128px;top:1861px"><svg width="14" height="14" viewBox="0 0 14 14"><path d="M5 2l5 5-5 5" fill="none" stroke="#222" stroke-width="2"/></svg></div>

<!-- Testimonials -->
<h2 class="abs head" style="top:2122px;font-size:38px">Client Success Stories</h2>
<div class="abs underline" style="top:2196px"></div>
<p class="abs centertxt" style="top:2228px;font-size:13px">Hear from our clients about their transformative journeys with us.</p>

<div class="abs review" style="left:112px"><p>The Wellness Barn has completely changed my approach to fitness. Their programs are tailored and effective!</p><div class="rule"></div><div class="avatar" role="img" aria-label="Client portrait"></div><div class="who"><b>Nina Brooks</b><span>Fitness Enthusiast</span><i class="stars" style="font-style:normal">★★★★★</i></div><div class="badge"></div></div>
<div class="abs review" style="left:446px"><p>I never thought I could regain my mobility. The physiotherapy classes here are a game changer!</p><div class="rule"></div><div class="avatar" role="img" aria-label="Client portrait"></div><div class="who"><b>Owen Hale</b><span>Retired Veteran</span><i class="stars" style="font-style:normal">★★★★★</i></div><div class="badge"></div></div>
<div class="abs review" style="left:780px"><p>I love how the wellness programs fit into my hectic schedule. I feel healthier and more energetic!</p><div class="rule"></div><div class="avatar" role="img" aria-label="Client portrait"></div><div class="who"><b>Lucy Marsh</b><span>Busy Mom</span><i class="stars" style="font-style:normal">★★★★★</i></div><div class="badge"></div></div>
<div class="abs" style="left:580px;top:2634px;width:13px;height:13px;border-radius:50%;background:#222"></div>
<div class="abs" style="left:605px;top:2634px;width:13px;height:13px;border-radius:50%;border:1.5px solid #222"></div>

<!-- Team -->
<section class="abs team" role="img" aria-label="Faint photo of a group exercising, tinted brown"></section>
<div class="abs centertxt" style="top:2818px;font-size:25px;color:#fff">Meet Our Team</div>
<h2 class="abs head" style="top:2862px;font-size:38px;color:#fff">Get to Know Us</h2>
<div class="abs underline" style="top:2934px;background:var(--brown);opacity:.8"></div>
<p class="abs centertxt" style="top:2956px;font-size:13px;color:#fff">Discover the dedicated professionals committed to your health.</p>
<div class="btn" style="left:510px;top:3007px;width:176px;height:44px;background:var(--green)">LEARN MORE</div>

<div class="abs" style="left:-40px;top:3093px;width:177px;height:279px;background:#a47d5a;border-radius:36px;opacity:.8"></div>
<div class="abs" style="left:1058px;top:3093px;width:180px;height:279px;background:#5c4030;border:5px solid #a47d5a;border-radius:36px"></div>
<div class="arrow light" style="left:37px;top:3204px;border-color:#d9c7a4"><svg width="14" height="14" viewBox="0 0 14 14"><path d="M9 2L4 7l5 5" fill="none" stroke="#d9c7a4" stroke-width="2"/></svg></div>
<div class="arrow" style="left:1126px;top:3204px;border-color:#fff"><svg width="14" height="14" viewBox="0 0 14 14"><path d="M5 2l5 5-5 5" fill="none" stroke="#fff" stroke-width="2"/></svg></div>

<div class="abs teamcard">
  <div class="abs" style="left:6px;top:6px;width:290px;height:258px;border-radius:30px;background:linear-gradient(#e8e4dc,#b8a890)" role="img" aria-label="Portrait of a smiling physiotherapist in a white coat"></div>
  <div class="abs" style="left:320px;top:38px;font-size:21px;font-weight:600">Dr. Clara Whitfield</div>
  <div class="abs" style="left:322px;top:80px;display:flex;gap:10px"><span style="width:32px;height:32px;border-radius:50%;border:1.5px solid #222"></span><span style="width:32px;height:32px;border-radius:50%;border:1.5px solid #222"></span></div>
  <p class="abs" style="left:322px;top:136px;width:300px;font-size:13px;line-height:27px">Dr. Clara specializes in sports rehabilitation and has over 10 years of experience in helping clients recover from injuries.</p>
</div>

<!-- FAQ -->
<h2 class="abs head" style="top:3540px;font-size:38px;left:-6px">FAQs</h2>
<div class="abs underline" style="top:3615px;left:500px"></div>
<p class="abs centertxt" style="top:3646px;left:240px;width:720px;font-size:13px;line-height:28px">Find answers to common questions about our health and wellness programs, services, and how we can support your journey to better health.</p>
<div class="btn" style="left:508px;top:3724px;width:176px;height:44px;background:var(--green)">VIEW PROGRAM</div>
<div class="abs" style="left:137px;top:3814px;width:397px;height:316px;background:linear-gradient(135deg,#6a3a22,#c8859a 60%,#3a2418)" role="img" aria-label="Spa setting with towels, herbal compresses and bath salts"></div>

<div class="abs faq-item" style="top:3818px">What types of programs do you offer?<svg width="30" height="18" viewBox="0 0 30 18"><path d="M2 2l13 13L28 2" fill="none" stroke="#222" stroke-width="3"/></svg></div>
<div class="abs faq-item" style="top:3905px">How can I get started?<svg width="30" height="18" viewBox="0 0 30 18"><path d="M2 2l13 13L28 2" fill="none" stroke="#222" stroke-width="3"/></svg></div>
<div class="abs faq-item" style="top:3992px">Are your classes suitable for beginners?<svg width="30" height="18" viewBox="0 0 30 18"><path d="M2 2l13 13L28 2" fill="none" stroke="#222" stroke-width="3"/></svg></div>

<!-- Footer -->
<footer class="abs site-footer">
  <div class="abs brandname" style="left:490px;top:118px;color:#fff;font-size:28px"><span class="dot" style="background:#fff;width:26px;height:26px"></span><span>The Wellness<br>Barn</span></div>
  <div class="abs" style="left:112px;top:340px;width:975px;height:1px;background:#8a9a86"></div>
  <div class="abs centertxt" style="top:372px;font-size:14px;color:#fff">Copyrights@2025 . The Wellness Barn .All Rights Reserved</div>
</footer>
<nav class="abs fnav"><span>HOME</span><span>ABOUT US</span><span>SERVICES</span><span>OUR PRODUCTS</span><span>TESTIMONIALS</span><span>CONTACT</span></nav>

</body>
</html>
```